Maple Grove Schools | brand new stationery!

We need stationery design with our new logo! Our company updated it's name and image and we like to incorporate the new one on our stationery, business cards and email signature. We are looking for fresh, new ideas!
Industry: Childcare, Elementary and Middle School
Company Name: Maple Grove Schools
Tagline: Bright Futures Start Here
Main colors: Blue, white and a little yellow
Star shape is something new for us! Do you see a way to incorporate it as a design element?

```html
<!DOCTYPE html>
<html lang="en">
<head>
<meta charset="utf-8">
<title>Maple Grove Schools – Business Card</title>
<link href="https://fonts.googleapis.com/css2?family=Josefin+Sans:wght@600&family=Figtree:wght@400;700&display=swap" rel="stylesheet">
<style>
  :root {
    --page: #e4e4e4;
    --navy-deep: #0a1f6e;
    --navy-mid: #0d2a86;
    --navy-light: #1550a8;
    --white: #ffffff;
    --yellow: #f7b81c;
    --card-dark: #231f20;
    --card-dark-edge: #3a3637;
    --silver: #a8a8aa;
  }
  * { margin: 0; padding: 0; box-sizing: border-box; }
  html, body { width: 1200px; height: 1200px; overflow: hidden; }
  body {
    background: var(--page);
    font-family: "Figtree", Arial, sans-serif;
    position: relative;
  }
  .card {
    position: absolute;
    left: 262px;
    width: 686px;
    height: 392px;
    border-radius: 20px;
    overflow: hidden;
  }
  .card-front { top: 165px; }
  .card-back {
    top: 653px;
    background: linear-gradient(160deg, var(--card-dark-edge) 0%, var(--card-dark) 45%, #171415 100%);
  }
  .front-pattern {
    position: absolute; inset: 0;
    background: linear-gradient(200deg, var(--navy-light) 0%, var(--navy-mid) 40%, var(--navy-deep) 100%);
  }
  .holder {
    position: absolute;
    right: calc(686px - 332px);
    top: 170px;
    text-align: right;
  }
  .holder-name {
    font-family: "Josefin Sans", Arial, sans-serif;
    font-weight: 600;
    font-size: 32px;
    letter-spacing: 0.5px;
    color: var(--white);
    line-height: 1;
  }
  .holder-title {
    margin-top: 6px;
    font-size: 15.5px;
    color: var(--yellow);
  }
  .divider {
    position: absolute;
    left: 354px; top: 128px;
    width: 1px; height: 135px;
    background: var(--white);
    opacity: 0.85;
  }
  .contact {
    position: absolute;
    left: 381px; top: 129px;
    list-style: none;
    color: var(--white);
    font-size: 15.5px;
    line-height: 19.5px;
  }
  .contact li { display: flex; align-items: flex-start; }
  .contact li.gap { margin-bottom: 8px; }
  .contact svg { width: 14px; height: 14px; margin: 3px 9px 0 0; flex: none; fill: var(--yellow); }
  .front-brand {
    position: absolute;
    left: 22px; bottom: 24px;
    display: flex; align-items: center; gap: 8px;
    color: var(--white);
    font-weight: 700;
    font-size: 14px;
    line-height: 1.15;
  }
  .brand-dot {
    width: 18px; height: 18px; border-radius: 50%;
    background: var(--yellow); flex: none;
  }
  .back-brand {
    position: absolute;
    left: 0; right: 0; top: 80px;
    text-align: center;
  }
  .back-brand .brand-dot {
    width: 44px; height: 44px;
    margin: 0 auto 34px;
  }
  .back-wordmark {
    color: var(--silver);
    font-weight: 700;
    font-size: 52px;
    line-height: 1.1;
    letter-spacing: 0.5px;
  }
</style>
</head>
<body>

<section class="card card-front">
  <div class="front-pattern" role="img" aria-label="Navy blue background scattered with small yellow stars"></div>

  <div class="holder">
    <p class="holder-name">DANIEL HARPER</p>
    <p class="holder-title">President</p>
  </div>

  <div class="divider"></div>

  <ul class="contact">
    <li class="gap">
      <svg viewBox="0 0 16 16"><path d="M8 0a5.5 5.5 0 0 0-5.5 5.5C2.5 10 8 16 8 16s5.5-6 5.5-10.5A5.5 5.5 0 0 0 8 0zm0 8a2.5 2.5 0 1 1 0-5 2.5 2.5 0 0 1 0 5z"/></svg>
      <span>1420 Willow Bend Road<br>Juneau, Alaska 99801</span>
    </li>
    <li>
      <svg viewBox="0 0 16 16"><path d="M3.6 1 6 3.8 4.6 5.6a9 9 0 0 0 5.8 5.8l1.8-1.4L15 12.4 13.4 15C6.8 15 1 9.2 1 2.6z"/></svg>
      <span>555-214-7730</span>
    </li>
    <li>
      <svg viewBox="0 0 16 16"><path d="M4 0h8a1 1 0 0 1 1 1v14a1 1 0 0 1-1 1H4a1 1 0 0 1-1-1V1a1 1 0 0 1 1-1zm1 2v10h6V2zm3 11a1 1 0 1 0 0 2 1 1 0 0 0 0-2z"/></svg>
      <span>555-318-4462</span>
    </li>
    <li>
      <svg viewBox="0 0 16 16"><path d="M4 1h6l2 2v3H4zM1 7h14v6H1zm3 4v4h8v-4z"/></svg>
      <span>555-276-9014</span>
    </li>
    <li>
      <svg viewBox="0 0 16 16"><path d="M1 4h14v9H1zm1.5 1L8 9l5.5-4z"/></svg>
      <span>info@maplegroveschools.com</span>
    </li>
    <li>
      <svg viewBox="0 0 16 16"><path d="M8 1a7 7 0 1 0 0 14A7 7 0 0 0 8 1zm0 1.5c.8 0 1.8 1.7 2 4H6c.2-2.3 1.2-4 2-4zM6 8h4c-.2 2.3-1.2 4-2 4s-1.8-1.7-2-4z"/></svg>
      <span>maplegroveschools.com</span>
    </li>
  </ul>

  <div class="front-brand">
    <span class="brand-dot"></span>
    <span>Maple Grove<br>Schools</span>
  </div>
</section>

<section class="card card-back">
  <div class="back-brand">
    <div class="brand-dot"></div>
    <p class="back-wordmark">Maple Grove<br>Schools</p>
  </div>
</section>

</body>
</html>
```